Business card por a urban DJ, up scale audience target

Need a sober design, modern, conservative colors but i can consider some options, y play rnb, hip hop, EDM and top40.

Business card for contact and personal info, double sided, use logo attrached please; im 42 so i need a card acording to my age an target audience.

Target Market(s)

Adult people, up scale audience

Industry/Entity Type

Music Download

Contact Information for Business Card

Cel (318) 4207265518 www.lumadrift.com

Requirements
Must have
• open mind
Nice to have
• open mind
Should not have
• DJ

```html
<!DOCTYPE html>
<html lang="en">
<head>
<meta charset="utf-8">
<title>Luma Drift — Business Card</title>
<link rel="stylesheet" href="https://fonts.googleapis.com/css2?family=Open+Sans:wght@400;700&display=swap">
<style>
  :root {
    --backdrop: #e6e2dc;
    --card-white: #ffffff;
    --card-charcoal: #333333;
    --band-black: #0a0a0a;
    --mark-dark: #2b2b2b;
    --mark-faint: #7a7a7a;
    --text-light: #ffffff;
    --shadow: rgba(0, 0, 0, 0.25);
  }
  * { box-sizing: border-box; margin: 0; padding: 0; }
  html, body {
    width: 1200px;
    height: 892px;
    overflow: hidden;
    background: var(--backdrop);
    font-family: "Open Sans", Arial, sans-serif;
  }
  .canvas {
    position: relative;
    width: 1200px;
    height: 892px;
  }
  .card {
    position: absolute;
    top: 291px;
    width: 540px;
    height: 310px;
    overflow: hidden;
    box-shadow: 0 10px 24px var(--shadow);
  }
  .card--front { left: 45px; background: var(--card-white); }
  .card--back  { left: 615px; background: var(--card-charcoal); }

  .front-shapes { position: absolute; inset: 0; }

  .brand-name {
    position: absolute;
    left: 38px;
    top: 22px;
    font-weight: 700;
    font-size: 84px;
    line-height: 1;
    letter-spacing: 2px;
    color: var(--mark-dark);
  }

  .contact-block {
    position: absolute;
    right: 26px;
    top: 190px;
    text-align: right;
    color: var(--text-light);
  }
  .person-name {
    font-weight: 700;
    font-size: 21px;
    line-height: 1.05;
  }
  .person-role {
    font-size: 14px;
    line-height: 1.2;
    margin-bottom: 8px;
  }
  .contact-list { list-style: none; }
  .contact-item {
    display: flex;
    justify-content: flex-end;
    align-items: center;
    gap: 8px;
    font-size: 12px;
    line-height: 17px;
  }
  .contact-icon {
    width: 12px;
    height: 12px;
    flex: none;
  }

  .back-name {
    position: absolute;
    inset: 0;
    display: flex;
    align-items: center;
    justify-content: center;
    font-weight: 700;
    font-size: 150px;
    letter-spacing: 4px;
    color: var(--mark-faint);
  }
</style>
</head>
<body>
<main class="canvas">

  <section class="card card--front" aria-label="Business card front">
    <svg class="front-shapes" width="540" height="310" viewBox="0 0 540 310" aria-hidden="true">
      <polygon points="0,218 540,176 540,310 0,310" fill="var(--card-charcoal)"/>
      <polygon points="0,206 540,164 540,176 0,218" fill="var(--band-black)"/>
    </svg>

    <div class="brand-name">LUMA</div>

    <div class="contact-block">
      <p class="person-name">Theo Vance</p>
      <p class="person-role">Managing Director</p>
      <ul class="contact-list">
        <li class="contact-item">(318) 4207265518
          <svg class="contact-icon" viewBox="0 0 12 12" aria-hidden="true"><rect width="12" height="12" fill="#fff"/><path d="M3 3.5h6l-0.8 5H3.8z" fill="#333"/></svg>
        </li>
        <li class="contact-item">info@lumadrift.com
          <svg class="contact-icon" viewBox="0 0 12 12" aria-hidden="true"><rect width="12" height="12" fill="#fff"/><rect x="2.5" y="3.5" width="7" height="5" fill="none" stroke="#333"/><path d="M2.5 3.5l3.5 3 3.5-3" fill="none" stroke="#333"/></svg>
        </li>
        <li class="contact-item">www.lumadrift.com
          <svg class="contact-icon" viewBox="0 0 12 12" aria-hidden="true"><rect width="12" height="12" fill="#fff"/><circle cx="6" cy="6" r="3.5" fill="none" stroke="#333"/><path d="M2.5 6h7M6 2.5v7" stroke="#333"/></svg>
        </li>
        <li class="contact-item">2450 Harbor Ave Suite 310, Riverton, GA 30412
          <svg class="contact-icon" viewBox="0 0 12 12" aria-hidden="true"><rect width="12" height="12" fill="#fff"/><path d="M6 10L3.5 6a2.5 2.5 0 1 1 5 0z" fill="#333"/><circle cx="6" cy="5.2" r="0.9" fill="#fff"/></svg>
        </li>
      </ul>
    </div>
  </section>

  <section class="card card--back" aria-label="Business card back">
    <div class="back-name">LUMA</div>
  </section>

</main>
</body>
</html>
```